Animal Eye Clinic needs a Business card

We are a new veterinary ophthalmology practice (Ridgeline Pet Vision Care) and we need a business card designed. We only see animal eyes - we are not a regular veterinary clinic. We already have a logo. We are looking for a professional, good looking business card to hand out to our clients. We are looking for something simple but professional and contemporary. Our logo is likely the only picture/graphic that needs to be on the card.
Updates

Contact Information for Business Card

Delia Vossman, BSc, DVM, MSc, DipACVO
Veterinary Ophthalmologist

Phone: 250.418.3927
Email: ridgelinepetvisioncare@mailbox-example.net
Website: ridgelinepetvisioncare-example.net
Address: 1874 Thornbury Rd
Kelowna, BC, V1X 4M9

Colors

Designer to choose colors to be used in the design.

Requirements
Must have
• Our logo (attached)

```html
<!DOCTYPE html>
<html lang="en">
<head>
<meta charset="utf-8">
<title>Ridgeline Pet Vision Care – Business Card</title>
<link rel="stylesheet" href="https://fonts.googleapis.com/css2?family=Lato:ital,wght@0,400;0,700;0,900;1,400&display=swap">
<style>
  :root {
    --teal: #1e9aab;
    --teal-deep: #17808f;
    --ink: #3b3f44;
    --muted: #6b7076;
    --rule: #c9cdd1;
    --paper: #ffffff;
    --stage: #e9ecee;
  }
  * { box-sizing: border-box; margin: 0; padding: 0; }
  html, body {
    width: 1200px; height: 878px; overflow: hidden;
    background: var(--stage);
    font-family: "Lato", Arial, sans-serif;
    color: var(--ink);
  }
  .sheet {
    width: 1200px; height: 878px;
    display: flex; align-items: center; justify-content: center; gap: 30px;
  }
  .card {
    position: relative;
    width: 560px; height: 320px;
    border-radius: 4px;
    box-shadow: 0 6px 18px rgba(0,0,0,.14);
    overflow: hidden;
  }

  /* Front */
  .card--front { background: var(--teal); }
  .brand {
    position: absolute; display: flex; align-items: center; gap: 12px;
    font-weight: 900; text-transform: uppercase; letter-spacing: .5px;
  }
  .brand__dot { border-radius: 50%; flex: none; }
  .card--front .brand { left: 70px; top: 138px; color: var(--paper); font-size: 27px; }
  .card--front .brand__dot { width: 40px; height: 40px; background: var(--paper); }

  /* Back */
  .card--back { background: var(--paper); }
  .person { position: absolute; left: 34px; top: 30px; }
  .person__name { color: var(--teal); font-weight: 900; font-size: 25px; }
  .person__creds { font-size: 10px; font-weight: 700; color: var(--ink); margin-left: 4px; }
  .person__title { font-size: 14px; color: var(--muted); margin-top: 2px; }

  .card--back .brand { right: 28px; top: 150px; color: var(--teal); font-size: 15px; gap: 8px; }
  .card--back .brand__dot { width: 26px; height: 26px; background: var(--teal); }

  .contact { position: absolute; left: 34px; top: 214px; list-style: none; }
  .contact li { display: flex; align-items: center; gap: 10px; font-size: 14.5px; line-height: 22px; color: var(--ink); }
  .contact svg { width: 14px; height: 14px; fill: var(--teal); flex: none; }
  .contact .web { color: var(--teal); }
  .contact .web span { color: var(--ink); }
  .divider { position: absolute; left: 34px; right: 34px; top: 283px; border-top: 1px solid var(--rule); }
  .address { position: absolute; left: 34px; top: 289px; display: flex; align-items: center; gap: 10px; font-size: 14.5px; }
  .address svg { width: 12px; height: 14px; fill: var(--teal); }
</style>
</head>
<body>
<main class="sheet">
  <section class="card card--front" aria-label="Card front">
    <div class="brand"><span class="brand__dot"></span>Ridgeline Pet Vision Care</div>
  </section>

  <section class="card card--back" aria-label="Card back">
    <div class="person">
      <p><span class="person__name">Delia Vossman,</span><span class="person__creds">BSc, DVM, MSc, DipACVO</span></p>
      <p class="person__title">Veterinary Ophthalmologist</p>
    </div>

    <div class="brand"><span class="brand__dot"></span>Ridgeline Pet Vision Care</div>

    <ul class="contact">
      <li><svg viewBox="0 0 24 24"><path d="M6.6 10.8a15 15 0 0 0 6.6 6.6l2.2-2.2a1 1 0 0 1 1-.25 11.4 11.4 0 0 0 3.6.57 1 1 0 0 1 1 1V20a1 1 0 0 1-1 1A17 17 0 0 1 3 4a1 1 0 0 1 1-1h3.5a1 1 0 0 1 1 1c0 1.25.2 2.45.57 3.57a1 1 0 0 1-.25 1z"/></svg>250.418.3927</li>
      <li><svg viewBox="0 0 24 24"><path d="M2 5h20v14H2zm2 2v.5l8 5 8-5V7l-8 5z"/></svg>ridgelinepetvisioncare@mailbox-example.net</li>
      <li><svg viewBox="0 0 24 24"><path d="M12 2a10 10 0 1 0 0 20 10 10 0 0 0 0-20zm0 2c.9 1.2 1.6 2.6 2 4h-4c.4-1.4 1.1-2.8 2-4zM4.3 14a8 8 0 0 1 0-4h3.5a16 16 0 0 0 0 4zm.8 2h3c.3 1.3.8 2.5 1.5 3.6A8 8 0 0 1 5.1 16zM8.1 8h-3a8 8 0 0 1 4.5-3.6C8.9 5.5 8.4 6.7 8.1 8zM12 20c-.9-1.2-1.6-2.6-2-4h4c-.4 1.4-1.1 2.8-2 4zm2.3-6H9.7a14 14 0 0 1 0-4h4.6a14 14 0 0 1 0 4zm.1 5.6c.7-1.1 1.2-2.3 1.5-3.6h3a8 8 0 0 1-4.5 3.6zm1.8-5.6a16 16 0 0 0 0-4h3.5a8 8 0 0 1 0 4z"/></svg><span class="web">www.ridgelinepetvisioncare-example<span>.net</span></span></li>
    </ul>
    <div class="divider"></div>
    <p class="address"><svg viewBox="0 0 12 16"><path d="M6 0a6 6 0 0 0-6 6c0 4.5 6 10 6 10s6-5.5 6-10a6 6 0 0 0-6-6zm0 8.5A2.5 2.5 0 1 1 6 3.5a2.5 2.5 0 0 1 0 5z"/></svg>1874 Thornbury Rd Kelowna, BC, V1X 4M9</p>
  </section>
</main>
</body>
</html>
```